Company or website name
- dalewintham.com
- Links to the website
- Vita Forge
- Describe your company and organization and target audience
- Founded by celebrity personal trainer and media personality Dale Wintham, Vita Forge provides high quality on-site fitness and wellness classes, and personal trainers for businesses and residential gyms throughout New York City. Our target audience are residents of high end buildings in NYC, that expect excellence and luxury
- The design should have the following
- This is a 24"x36" Poster for a complimentary event at a high end building. I would like the poster to look high end, luxury and simple and chique. The words should be clear and easy to read. It would be great to have a final copy that we can send to the printer and one which we can edit for future events Here is the text: The Halcott Spires Gym Complimentary Fitness & Wellness Event Complimentary Yoga, Pilates & Interval Training Bootcamp Classes PLUS: 30 Minute Private Training Sessions *Kids Karate Classes Also Available Saturday May 18th, 25th & June 1st Time: 9:00am - 12:15pm Halcott Spires Gym Schedule: 9:00am - 9:30am Yoga 9:45am - 10:15am Interval Training Bootcamp 11:45am -12:15pm Pilates 9:00am - 12:00pm Private Training Sessions Special Introductory Rate on Future Packages During Promotion www.Vitaforge.tv Info@vitaforge.tv
- Other Facts

```html
<!DOCTYPE html>
<html lang="en">
<head>
<meta charset="utf-8">
<title>The Halcott Spires Gym – Complimentary Fitness &amp; Wellness Event</title>
<link rel="stylesheet" href="https://fonts.googleapis.com/css2?family=Mulish:wght@400;600;700;800&display=swap">
<style>
  :root {
    --page: #ffffff;
    --ink: #000000;
    --white: #ffffff;
    --blue-top: #1f9fe0;
    --blue-bottom: #1a5b94;
    --green-top: #8fb33a;
    --green-bottom: #5f8a26;
    --burst: #d8141b;
    --photo-light: #4a4a4a;
    --photo-dark: #0d0d0d;
  }
  * { margin: 0; padding: 0; box-sizing: border-box; }
  html, body {
    width: 1200px; height: 960px; overflow: hidden;
    background: var(--page);
    font-family: "Mulish", "Century Gothic", sans-serif;
  }
  .poster {
    position: absolute; left: 280px; top: 0;
    width: 640px; height: 960px;
    background: var(--ink);
    color: var(--white);
    overflow: hidden;
  }
  .top-tab {
    position: absolute; left: 48px; top: -4px; width: 546px; height: 25px;
    background: linear-gradient(var(--green-top), var(--green-bottom));
    border: 3px solid var(--white);
  }
  .event-header {
    position: absolute; left: 0; top: 25px; width: 640px; height: 100px;
    background: linear-gradient(var(--blue-top), var(--blue-bottom));
    border-bottom: 3px solid var(--white);
    text-align: center;
  }
  .event-header .venue {
    font-weight: 800; font-size: 37px; letter-spacing: 0.3px;
    margin-top: 12px; line-height: 44px;
  }
  .event-header .event-name {
    font-weight: 400; font-size: 24px; line-height: 30px; letter-spacing: 0.4px;
  }
  .classes-box {
    position: absolute; left: 48px; top: 129px; width: 546px; height: 76px;
    background: linear-gradient(var(--green-top), var(--green-bottom));
    border: 3px solid var(--white);
    text-align: center;
    font-weight: 800; font-size: 20px; line-height: 26px;
    padding-top: 9px;
  }
  .athlete-photo {
    position: absolute; left: 66px; top: 231px; width: 196px; height: 484px;
    background: radial-gradient(ellipse at 50% 45%, var(--photo-light) 0%, #262626 45%, var(--photo-dark) 80%);
    border-radius: 40px;
  }
  .session-offer {
    position: absolute; left: 384px; top: 252px;
    line-height: 1;
  }
  .session-offer .minutes { font-weight: 800; font-size: 34px; }
  .session-offer .unit { font-weight: 800; font-size: 23px; margin-top: 2px; }
  .session-offer .label { font-weight: 400; font-size: 24px; line-height: 30px; margin-top: 4px; }
  .plus-burst {
    position: absolute; left: 487px; top: 240px; width: 100px; height: 72px;
  }
  .brand-name {
    position: absolute; left: 337px; top: 420px; width: 270px;
    font-weight: 800; font-size: 74px; line-height: 82px; letter-spacing: 1px;
    white-space: nowrap;
  }
  .brand-rule {
    position: absolute; left: 337px; width: 270px; height: 2px; background: var(--white);
  }
  .brand-rule.upper { top: 621px; }
  .brand-rule.lower { top: 668px; }
  .brand-caption {
    position: absolute; left: 337px; top: 626px; width: 270px;
    font-weight: 800; font-size: 33px; line-height: 40px;
    white-space: nowrap;
  }
  .brand-byline {
    position: absolute; left: 337px; top: 677px; width: 270px;
    font-weight: 400; font-size: 26px; line-height: 32px; letter-spacing: 0.3px;
    white-space: nowrap;
  }
  .schedule {
    position: absolute; right: 39px; top: 731px;
    text-align: right; font-size: 15.5px; line-height: 21.5px; font-weight: 400;
    white-space: nowrap;
  }
  .schedule b { font-weight: 800; }
  .footer-band {
    position: absolute; left: 0; top: 866px; width: 640px; height: 72px;
    background: linear-gradient(var(--green-top), var(--green-bottom));
    border-top: 3px solid var(--white);
    border-bottom: 3px solid var(--white);
    text-align: center; font-size: 15.5px; line-height: 21px;
    padding-top: 12px;
  }
  .footer-band .contact { font-weight: 800; }
  .footer-band .contact span { margin: 0 4px; }
</style>
</head>
<body>
  <main class="poster">
    <div class="top-tab"></div>

    <header class="event-header">
      <h1 class="venue">THE HALCOTT SPIRES GYM</h1>
      <p class="event-name">COMPLIMENTARY FITNESS &amp; WELLNESS EVENT</p>
    </header>

    <section class="classes-box">
      COMPLIMENTARY YOGA, PILATES &amp;<br>INTERVAL TRAINING BOOTCAMP CLASSES
    </section>

    <div class="athlete-photo" role="img" aria-label="Photo of a female athlete in black sportswear throwing a punch with a raised knee"></div>

    <div class="session-offer">
      <div class="minutes">30</div>
      <div class="unit">MINUTE</div>
      <div class="label">PRIVATE TRAINING<br>SESSIONS</div>
    </div>

    <svg class="plus-burst" viewBox="0 0 100 72" aria-label="Plus">
      <polygon fill="var(--burst)" points="50,2 58,12 70,5 73,17 87,14 84,27 98,31 88,40 96,52 82,54 82,68 69,62 60,72 50,63 40,72 31,62 18,68 18,54 4,52 12,40 2,31 16,27 13,14 27,17 30,5 42,12"/>
      <text x="50" y="45" text-anchor="middle" transform="rotate(-12 50 38)" fill="#ffffff" font-family="Mulish, sans-serif" font-weight="800" font-size="23">PLUS</text>
    </svg>

    <div class="brand-name">VITA<br>FORGE</div>

    <div class="brand-rule upper"></div>
    <div class="brand-caption">VITA FORGE</div>
    <div class="brand-rule lower"></div>
    <div class="brand-byline">BY DALE WINTHAM</div>

    <section class="schedule">
      <b>*Kids Karate Classes Also Available</b><br>
      Saturday May 18th, 25th &amp; June 1st Time: <b>9:00am - 12:15pm</b><br>
      Halcott Spires Gym Schedule: <b>9:00am - 9:30am</b><br>
      Yoga 9:45am - 10:15am Interval Training Bootcamp <b>11:45am -12:15pm</b><br>
      Pilates <b>9:00am - 12:00pm</b>
    </section>

    <footer class="footer-band">
      <p>Special Introductory Rate on Future Packages During Promotion</p>
      <p class="contact"><span>www.Vitaforge.tv</span><span>Info@vitaforge.tv</span></p>
    </footer>
  </main>
</body>
</html>
```